Looking for a modern, Professional business card design

We have a simple business card, but are looking for a more modern, professional look. A sample of the basic card is attached as well as the logo. We would also like to add that we offer:
Struggling with your finances?
- Learn to become debt free
- Discover the power of cash
- Control your money instead of it controlling you
Let us help you achieve a new level of financial freedom!
Also, we would like to have a "SPECIAL OFFER!: FREE 30 minute consultation"
Financial Planning

```html
<!DOCTYPE html>
<html lang="en">
<head>
<meta charset="utf-8">
<title>Steadfast Money Coaching – Business Card</title>
<link href="https://fonts.googleapis.com/css2?family=Jost:wght@400;500;700&family=Russo+One&display=swap" rel="stylesheet">
<style>
  :root {
    --stage: #e9ebe6;
    --lime: #8cc63f;
    --leaf: #2f9a3f;
    --white: #ffffff;
    --ink: #1c1c1c;
    --soft-ink: #3a3a3a;
  }
  * { box-sizing: border-box; margin: 0; padding: 0; }
  html, body { width: 1200px; height: 900px; overflow: hidden; }
  body {
    background: var(--stage);
    font-family: "Jost", Arial, sans-serif;
    position: relative;
  }
  .card {
    position: absolute;
    left: 250px;
    width: 700px;
    height: 400px;
    border-radius: 22px;
    overflow: hidden;
    box-shadow: 0 6px 18px rgba(0,0,0,0.18);
  }

  /* Back side */
  .card-back { top: 35px; background: var(--lime); color: var(--white); text-align: center; }
  .back-brand {
    position: absolute; top: 62px; left: 0; right: 0;
    display: flex; justify-content: center; align-items: center; gap: 12px;
    font-size: 30px; font-weight: 700; letter-spacing: 1px;
  }
  .brand-dot { width: 18px; height: 18px; border-radius: 50%; background: currentColor; flex: none; }
  .pitch { position: absolute; top: 170px; left: 0; right: 0; font-size: 21px; line-height: 1.45; }
  .pitch strong { color: var(--ink); font-weight: 700; }
  .back-band { position: absolute; left: 0; right: 0; bottom: 0; height: 24px; display: flex; }
  .back-band .dark { width: 64%; background: var(--leaf); }
  .back-band .light { flex: 1; background: var(--white); }

  /* Front side */
  .card-front { top: 465px; background: var(--white); }
  .front-brand {
    position: absolute; top: 96px; left: 38px;
    display: flex; align-items: center; gap: 12px;
    color: var(--leaf);
  }
  .front-brand .name { font-size: 30px; font-weight: 700; line-height: 1.1; width: 250px; }
  .tagline { position: absolute; top: 178px; left: 68px; font-size: 11px; color: var(--soft-ink); }
  .person { position: absolute; top: 58px; right: 38px; width: 300px; text-align: right; }
  .person-name { font-family: "Russo One", Arial, sans-serif; font-size: 28px; color: var(--lime); letter-spacing: 1px; white-space: nowrap; }
  .person-rule { height: 2px; background: var(--leaf); margin: 4px 0 6px; width: 290px; margin-left: auto; }
  .person-title { font-family: "Russo One", Arial, sans-serif; font-size: 15px; color: var(--ink); letter-spacing: 0.5px; white-space: nowrap; }
  .offer { position: absolute; top: 158px; right: 38px; text-align: right; color: var(--lime); font-size: 22px; line-height: 1.1; }
  .offer-label { font-family: "Russo One", Arial, sans-serif; font-size: 17px; }
  .offer-free { color: var(--ink); font-weight: 500; }
  .mid-band { position: absolute; left: 0; right: 0; top: 222px; height: 14px; display: flex; }
  .mid-band .dark { width: 66%; background: var(--leaf); margin-left: 38px; }
  .mid-band .light { flex: 1; background: var(--lime); }
  .contacts { position: absolute; left: 38px; top: 256px; list-style: none; font-size: 21px; color: var(--ink); line-height: 1.55; }
  .contacts li { display: flex; align-items: center; gap: 14px; }
  .contacts svg { width: 18px; height: 18px; flex: none; }
  .contacts .web-domain { color: var(--lime); }
  .foot-band { position: absolute; left: 0; right: 0; bottom: 0; height: 18px; display: flex; }
  .foot-band .light { width: 66%; background: var(--white); }
  .foot-band .dark { flex: 1; background: var(--leaf); }
  .foot-band .lime { position: absolute; inset: 0 34% 0 0; background: var(--lime); }
</style>
</head>
<body>

<section class="card card-back" aria-label="Card back">
  <div class="back-brand"><span class="brand-dot"></span><span>Steadfast Money Coaching</span></div>
  <div class="pitch">
    <p>STRUGGLING WITH YOUR <strong>FINANCES?</strong></p>
    <p>Learn to become debt free</p>
    <p>Discover the power of cash</p>
    <p>Control your money instead of it controlling you</p>
    <p>Let us help you achieve a new level of financial <strong>FREEDOM!</strong></p>
  </div>
  <div class="back-band"><span class="dark"></span><span class="light"></span></div>
</section>

<section class="card card-front" aria-label="Card front">
  <div class="front-brand"><span class="brand-dot"></span><span class="name">Steadfast Money Coaching</span></div>
  <p class="tagline">Achieve a new level of personal freedom</p>

  <div class="person">
    <p class="person-name">DANIEL R. HAYES</p>
    <div class="person-rule"></div>
    <p class="person-title">PERSONAL FINANCIAL COACH</p>
  </div>

  <p class="offer"><span class="offer-label">SPECIAL OFFER!</span> <span class="offer-free">FREE 30</span><br>minute consultation</p>

  <div class="mid-band"><span class="dark"></span><span class="light"></span></div>

  <ul class="contacts">
    <li>
      <svg viewBox="0 0 18 18" aria-hidden="true"><rect x="5" y="2" width="8" height="14" rx="1.5" fill="none" stroke="#8cc63f" stroke-width="1.6"/><circle cx="9" cy="13.5" r="0.9" fill="#8cc63f"/></svg>
      <span>(205) 555-0148</span>
    </li>
    <li>
      <svg viewBox="0 0 18 18" aria-hidden="true"><rect x="2" y="4" width="14" height="10" rx="1" fill="none" stroke="#8cc63f" stroke-width="1.6"/><path d="M2 5l7 5 7-5" fill="none" stroke="#8cc63f" stroke-width="1.6"/></svg>
      <span>daniel@steadfastmoneycoach.com</span>
    </li>
    <li>
      <svg viewBox="0 0 18 18" aria-hidden="true"><circle cx="9" cy="9" r="7" fill="none" stroke="#8cc63f" stroke-width="1.5"/><ellipse cx="9" cy="9" rx="3" ry="7" fill="none" stroke="#8cc63f" stroke-width="1.2"/><path d="M2 9h14" stroke="#8cc63f" stroke-width="1.2"/></svg>
      <span>www.<span class="web-domain">steadfastmoneycoach</span>.com</span>
    </li>
  </ul>

  <div class="foot-band"><span class="light"></span><span class="dark"></span><span class="lime"></span></div>
</section>

</body>
</html>
```